Blood Testing Health App

We are looking for a graphics designer to create a web app for us so that we may insert it into a health management website system.
For branding purposes we are at www.Vantiqor.com and we are revamping our website... Example of new colors attached.
How we work...
We are a blood testing company based in the USA.
We offer a blood testing service nationwide in the USA.
We allow customers to order tests directly from us, visit a lab, have their blood drawn, or submit a urine sample, the lab tests it and they send the results back to our computer system and we share it with the customer.
The benefits of this are the customer does not need to go to the doctor and pay for the doctors visit to order these tests, which save them money. The tests are cheaper than going through the doctor. The customer simply uses us to get the test and the results and they can then take the results to their doctor... this process has saved them money. Others may be interested in regular check ups for blood work etc... and this allows them to do it with out needing a doctor, or if you have no insurance, this is a cheaper option too. We are quicker than a doctor, customers do not need appointments etc.
Hopefully you now have a better understanding as to what we do.
Here is the spec.
The app screen size is 750 px wide by 700 px high. ( A pdf is attached to show where the app is going to go, it is on page 3 of the pdf) The customer will have the ability to scroll… therefore the length of the page can be longer.
The app will consist of the following sections
Entry Page –
This will be the first page the user sees upon opening the app. This will be where they are directed from to the sections of the app discussed below. This needs to be branded for VantiQor with a modern look.
1 – Order Test (Giving them the ability to purchase a blood test within the app)
2 – VantiQor Dashboard (A dashboard that has everything they could need to use our service_
How it works Section on entry page – this will be a simple set of graphics showing how the service works. We already have the graphics for this, they do not need to be built again. They are attached to this brief
Basic structure of sections –
Order Test –
This page contains all tests, filed in categories – and Sub categories – Each test needs a link to an Information section – Price – Buy Now – Cart Process
VantiQor Dashboard –
A page of icons along the top of the app
- My Confirmation
- My Nearest Lab
- My Receipt
- My Orders
- My Account
- My Results
- My Inbox
- Contact Us
Sections in more detail -
Order A Test –
Show all categories/ sub categories – There are 23 categories, 14 sub categories, and within these categories are 300 tests - Here is the information for the categories etc - http://www.vantiqor.com/panels.aspx?PanelGroupID=4 Just in case it helps :)
We need to present this in a graphic format that is spacious, modern (brimlake, kivvo web appearance is the direction we are going for) We need it to be clear and not overwhelming to the customer.
Functionality idea…
Customer clicks category/ subcategory and tests appear.
Customer sees small 35 word description. For more information the test opens into a lightbox or expand the container which ever graphic designer believes to be most visually appealing
Buy Now must always be visible, along with price of the test
Buying process explained – Customer clicks buy now –
They are then taken to a Review Order screen ( This contains Order summary and choose payment method – insert payment details )
– Confirm payment –
Confirmation screen appears, thanking them.
They are then taken to the VantiQor Dashboard...
VantiQor Dashboard –
"My Confirmation" - Print Confirmation Order (PDF is in brief, we want this web based not a pdf download)
"My Nearest Lab Location" - This does not need to be designed because the web developer has this part under control, but we do need the icon in the dashboard
"My Receipt" - Print receipt - This does not exist in our system yet. So we need to create this from scratch - It will need to have - The test they are purchasing and the amount of the test - The customers name - The order ID - Must provide printer friendly option too
"My Orders" - This will have a list of orders - At the end of each order will be a status update of either "Test results" "Open order"
A graphic table format would be perfect. This will be linked to relevant results if they have been received. I have also attached a version of what the customer currently sees on our website. We know it is nasty ;) We are redesigning... but the information is there for this section to help design it with the right info. If the results are ready it will say in this list.
"Results Ready" will be a link to show those results once the customer has clicked the link, and the results will appear in the app, under the icons. There must be a printer friendly version too.
"My Results" Developer will sort this page out but we need the icon... It will be exactly like my orders but only show test results
"My Account" - This will be a place for them to update their personal information - Name, DOB, Address, Email Address
"My Inbox" - An inbox interface - Our way of contacting the customer for promotions we are running etc – We need a design of how this screen will appear. We also need the icon in the dashboard to have a notification on it if there are messages in the customers inbox. A little red 1, or circle with number of messages in the inbox.
"Customer Service" - This does not need to be designed because the web developer has this part under control, but we do need the icon in the dashboard
Icons appear along the top of app ( example - Mac icons/ iphone app icons) When the customer clicks an icon the content always appears below the icons
Here is more information for the icons and what should appear when each icon is clicked.
Screens to be designed –
Entry Page
Order A Test Page
Review Order Screen/Payment Screen - Show a lightbox that shows payment has been confirmed. Customer clicks close and are on the Confirmation Screen
VantiQor Dashboard - Screens mentioned in detail above
We can't wait to see your designs!
Please email any questions.
Hi all this is the first time we have used pixel harbor and understand the budget was too low for this project. We have now increased the budget to $2,000 and extended the deadline by another week
Hi all we are receiving some really great designs. I just added an example of the space that the web app will be going into... It is called "morvelapp.pdf"
Hi guys updated the brief. Hopefully this will help with the dashboard part of the design

```html
<!DOCTYPE html>
<html lang="en">
<head>
<meta charset="utf-8">
<title>VantiQor – Order Summary</title>
<link rel="stylesheet" href="https://fonts.googleapis.com/css2?family=Open+Sans:wght@400;600;700&display=swap">
<style>
  :root {
    --brand-green: #7dbf37;
    --brand-green-dark: #6aa82a;
    --ink: #2b2b2b;
    --ink-soft: #333333;
    --panel-grey: #ebebeb;
    --table-head: #535a53;
    --row-line: #e6e6e6;
    --link-blue: #1f70c1;
    --total-orange: #ef4e0f;
    --btn-orange-top: #ff7a26;
    --btn-orange-bottom: #ee4d05;
    --btn-blue-top: #4a9ae6;
    --btn-blue-bottom: #1f6fc6;
    --nav-top: #fafafa;
    --nav-bottom: #e9e9e9;
    --white: #ffffff;
  }
  * { box-sizing: border-box; margin: 0; padding: 0; }
  html, body {
    width: 1200px; height: 1163px; overflow: hidden;
    background: var(--white);
    font-family: "Open Sans", Arial, sans-serif;
    color: var(--ink-soft);
  }
  .app { position: relative; width: 1200px; height: 1163px; }

  /* Header */
  .brand {
    position: absolute; left: 29px; top: 60px;
    display: flex; align-items: flex-end; gap: 14px;
  }
  .brand-mark { width: 34px; height: 34px; background: var(--brand-green); margin-bottom: 14px; }
  .brand-name {
    font-size: 64px; font-weight: 400; letter-spacing: 1px;
    color: var(--ink); line-height: 1;
  }

  .main-nav { position: absolute; left: 534px; top: 45px; display: flex; gap: 21px; }
  .nav-tile {
    width: 207px; height: 104px; border-radius: 6px;
    border: 1px solid #d9d9d9;
    background: linear-gradient(var(--nav-top), var(--nav-bottom));
    display: flex; flex-direction: column; align-items: center; justify-content: center;
    gap: 8px; color: var(--brand-green); font-size: 17px; text-decoration: none;
  }
  .nav-tile svg { display: block; }

  .social { position: absolute; left: 1010px; top: 101px; display: flex; gap: 10px; }
  .social-dot { width: 45px; height: 45px; border-radius: 50%; background: var(--brand-green); }

  /* Order summary */
  .checkout-panel {
    position: absolute; left: 29px; top: 190px; width: 1139px; height: 482px;
    background: var(--panel-grey); border-radius: 13px;
  }
  .summary-card {
    position: absolute; left: 17px; top: 18px; width: 1103px; height: 365px;
    background: var(--white); border-radius: 12px; overflow: hidden;
  }
  .summary-title {
    height: 75px; background: var(--brand-green);
    color: var(--white); font-size: 29px; font-weight: 400;
    padding-left: 26px; line-height: 75px;
  }
  .summary-table { width: 100%; border-collapse: collapse; }
  .summary-table th {
    background: var(--table-head); color: var(--white);
    font-weight: 400; font-size: 21px; text-align: left; height: 59px;
  }
  .summary-table td { font-size: 18px; color: var(--ink-soft); border-bottom: 1px solid var(--row-line); }
  .summary-table tr:last-child td { border-bottom: none; }
  .col-name { padding-left: 24px; width: 732px; }
  .col-qty { width: 171px; }
  .row-test td { height: 56px; }
  .row-extra td { height: 54px; }
  .test-link { color: var(--link-blue); font-size: 21px; text-decoration: none; }
  .total-amount { color: var(--total-orange); font-weight: 700; }

  .pay-actions { position: absolute; top: 405px; right: 16px; display: flex; gap: 18px; }
  .pay-btn {
    height: 56px; border-radius: 5px; color: var(--white);
    font-size: 21px; font-weight: 700; text-decoration: none;
    display: flex; align-items: center; gap: 14px; padding: 0 22px 0 14px;
  }
  .pay-card { width: 350px; background: linear-gradient(var(--btn-orange-top), var(--btn-orange-bottom)); border: 2px solid #ffb27a; }
  .pay-wallet { width: 248px; background: linear-gradient(var(--btn-blue-top), var(--btn-blue-bottom)); border: 2px solid #8cc2f2; }
  .pay-btn svg { flex: none; }
</style>
</head>
<body>
<div class="app">
  <header>
    <div class="brand">
      <span class="brand-mark"></span>
      <span class="brand-name">VANTIQOR</span>
    </div>

    <nav class="main-nav">
      <a class="nav-tile" href="#">
        <svg width="46" height="38" viewBox="0 0 46 38" aria-hidden="true">
          <rect x="6" y="2" width="34" height="26" rx="3" fill="#7dbf37"/>
          <rect x="10" y="6" width="26" height="18" fill="#a8d872"/>
          <rect x="1" y="30" width="44" height="5" rx="2" fill="#7dbf37"/>
        </svg>
        ORDER A TEST
      </a>
      <a class="nav-tile" href="#">
        <svg width="42" height="42" viewBox="0 0 42 42" aria-hidden="true">
          <rect x="12" y="2" width="28" height="24" fill="none" stroke="#7dbf37" stroke-width="4"/>
          <rect x="3" y="14" width="28" height="25" fill="#fff" stroke="#7dbf37" stroke-width="4"/>
          <rect x="3" y="14" width="28" height="6" fill="#7dbf37"/>
        </svg>
        DASHBOARD
      </a>
    </nav>

    <div class="social" aria-label="Social links">
      <span class="social-dot"></span>
      <span class="social-dot"></span>
      <span class="social-dot"></span>
    </div>
  </header>

  <main class="checkout-panel">
    <section class="summary-card">
      <h1 class="summary-title">ORDER SUMMARY</h1>
      <table class="summary-table">
        <thead>
          <tr>
            <th class="col-name">Test Name</th>
            <th class="col-qty">Qty</th>
            <th>Price</th>
          </tr>
        </thead>
        <tbody>
          <tr class="row-test">
            <td class="col-name"><a class="test-link" href="#">COMPREHENSIVE Erectile Dysfunction Profile</a></td>
            <td class="col-qty">1</td>
            <td>$75.00</td>
          </tr>
          <tr class="row-test">
            <td class="col-name"><a class="test-link" href="#">Healthy Male Checkup</a></td>
            <td class="col-qty">1</td>
            <td>$180.00</td>
          </tr>
          <tr class="row-extra">
            <td class="col-name">Discount Coupon</td>
            <td class="col-qty"></td>
            <td>$50.00</td>
          </tr>
          <tr class="row-extra">
            <td class="col-name">You have 2 items in your cart with <strong>TOTAL</strong> of</td>
            <td class="col-qty"></td>
            <td class="total-amount">$205.00</td>
          </tr>
        </tbody>
      </table>
    </section>

    <div class="pay-actions">
      <a class="pay-btn pay-card" href="#">
        <svg width="30" height="30" viewBox="0 0 30 30" aria-hidden="true">
          <circle cx="15" cy="15" r="14" fill="#8a2a00" opacity="0.55"/>
          <path d="M8 15h12M15 9l6 6-6 6" stroke="#ffd2b0" stroke-width="3" fill="none" stroke-linecap="round" stroke-linejoin="round"/>
        </svg>
        Pay with Credit/HSA Card
      </a>
      <a class="pay-btn pay-wallet" href="#">
        <svg width="30" height="30" viewBox="0 0 30 30" aria-hidden="true">
          <circle cx="15" cy="15" r="14" fill="#0c3f7a" opacity="0.6"/>
          <path d="M8 15h12M15 9l6 6-6 6" stroke="#cfe6ff" stroke-width="3" fill="none" stroke-linecap="round" stroke-linejoin="round"/>
        </svg>
        Pay with Walletly
      </a>
    </div>
  </main>
</div>
</body>
</html>
```